Veltrane Group Business Card Design

The CEO is looking for a new trendy look for his business card.
You can stay with current branding or come up with something new/creative. It can be 3D, including Medical Office buildings. You can use our logo in a variety of colors. Please include name, title, company name, company website, email address, cell number

Target Market(s)

Real Estate Development and Construction

Industry/Entity Type

Health care real estate

Contact Information for Business Card

Rohesh Kamdar, CEO M-604.781.2249 E-roheshkamdar@veltrane.com Address:4180 Lindqvist Ave, Tampa, FL 33482 www.veltrane.com

Font styles to use
Other font styles liked:
• Be creative

Requirements
Must have
• Creative, trendy look
Nice to have
• Please go to our website to get a feel- www. veltrane.com
Should not have
• small fonts

```html
<!DOCTYPE html>
<html lang="en">
<head>
<meta charset="utf-8">
<title>Veltrane Group Business Card</title>
<link href="https://fonts.googleapis.com/css2?family=Montserrat:wght@400;600;800&display=swap" rel="stylesheet">
<style>
  :root {
    --backdrop: #d2cab8;
    --card: #181818;
    --ink: #ffffff;
    --brand-red: #b01f28;
    --brand-navy: #1f2c4f;
  }
  html, body {
    margin: 0;
    padding: 0;
    width: 1116px;
    height: 1200px;
    overflow: hidden;
    background: var(--backdrop);
    font-family: "Montserrat", Arial, sans-serif;
  }
  .card {
    position: absolute;
    left: 217px;
    width: 682px;
    height: 390px;
    background: var(--card);
    color: var(--ink);
    box-shadow: 0 14px 28px rgba(0,0,0,0.35);
  }
  .card--front { top: 184px; }
  .card--back { top: 625px; }

  .company-name {
    position: absolute;
    left: 28px;
    top: 34px;
    margin: 0;
    font-size: 50px;
    font-weight: 800;
    letter-spacing: -1px;
    line-height: 1;
    color: var(--ink);
  }
  .person {
    position: absolute;
    right: 25px;
    top: 174px;
    text-align: right;
  }
  .person__name {
    margin: 0;
    font-size: 28px;
    font-weight: 600;
    letter-spacing: 0.5px;
    line-height: 1.1;
  }
  .person__title {
    margin: 4px 6px 0 0;
    font-size: 20px;
    font-weight: 400;
  }
  .accent-bar {
    position: absolute;
    right: 0;
    top: 170px;
    width: 14px;
    height: 52px;
    background: var(--ink);
  }
  .address {
    position: absolute;
    left: 28px;
    top: 205px;
    margin: 0;
    font-size: 20px;
    font-style: normal;
    line-height: 31px;
  }
  .contacts {
    position: absolute;
    left: 28px;
    top: 287px;
    margin: 0;
    padding: 0;
    list-style: none;
    font-size: 20px;
    line-height: 30px;
  }
  .contacts li {
    display: flex;
    align-items: center;
    gap: 8px;
  }
  .contacts svg { width: 14px; height: 14px; fill: var(--ink); }

  .brand-mark {
    position: absolute;
    inset: 0;
    display: flex;
    align-items: center;
    justify-content: center;
    gap: 18px;
  }
  .brand-mark__text {
    margin: 0;
    font-size: 60px;
    font-weight: 800;
    letter-spacing: -1px;
    line-height: 1;
    color: var(--brand-red);
  }
  .brand-mark__square {
    width: 40px;
    height: 40px;
    background: var(--brand-navy);
  }
</style>
</head>
<body>
  <section class="card card--front">
    <h1 class="company-name">Veltrane Group</h1>
    <div class="person">
      <p class="person__name">ROHESH KAMDAR</p>
      <p class="person__title">CEO</p>
    </div>
    <div class="accent-bar"></div>
    <address class="address">4180 Lindqvist Ave,<br>Tampa, FL 33482</address>
    <ul class="contacts">
      <li>
        <svg viewBox="0 0 14 14" aria-hidden="true"><path d="M3 0h8a1 1 0 0 1 1 1v12a1 1 0 0 1-1 1H3a1 1 0 0 1-1-1V1a1 1 0 0 1 1-1zm1 2v8h6V2zm3 9a1 1 0 1 0 0 2 1 1 0 0 0 0-2z"/></svg>
        604.781.2249
      </li>
      <li>
        <svg viewBox="0 0 14 14" aria-hidden="true"><path d="M0 3h14v1L7 8 0 4zm0 2.3 7 4 7-4V11H0z"/></svg>
        roheshkamdar@veltrane.com
      </li>
      <li>
        <svg viewBox="0 0 14 14" aria-hidden="true"><circle cx="7" cy="7" r="6.5"/><path d="M3 4c2 0 2 2 4 2s1 3-1 3-1 3-2 3C3 11 2 8 3 4zm6-2c1 1 3 2 2 4-1 1-3 0-2-4z" fill="#181818"/></svg>
        www.veltrane.com
      </li>
    </ul>
  </section>

  <section class="card card--back">
    <div class="brand-mark">
      <p class="brand-mark__text">Veltrane Group</p>
      <div class="brand-mark__square"></div>
    </div>
  </section>
</body>
</html>
```